Business Card Re-Design/Update

We'd like to update out business cards. I've included our current "Style guide" which has the colour scheme of the organisation in it. I've also included the branding files with logos etc in them.

I've also included a copy of one of our existing cards so that you can see how ugly/dated they look. I'd like a fresh modern corporate look.

Target Market(s)

These are for our clients, potential clients, industry contacts - like all business cards

Contact Information for Business Card

Name
Position
Company Address - Level 1, 47 Fernby Street, Carlow Qld 4072
Direct Phone
mobile
Email
Website -www.korvalit.com.au
Logo

Colors

Designer to choose colors to be used in the design.

Requirements
Must have
• Main Logo
• Cards will need to be editable to be able to personalize them for each new employee.
Nice to have
• The MapOut, ShipWell, KeepSteady would be okay to have if they can be sensibly and professionally added to the look without detracting from the main imagery.
• Maybe they could go on the back of the card? will leave this to your creative discretion as to whether/where they fit.
Should not have
• Should not have decorative or script fonts

```html
<!DOCTYPE html>
<html lang="en">
<head>
<meta charset="utf-8">
<title>Korvalit business card</title>
<link rel="stylesheet" href="https://fonts.googleapis.com/css2?family=Roboto:wght@400;500;700&family=Roboto+Condensed:wght@400;700&display=swap">
<style>
  :root {
    --brand-red: #d0161f;
    --brand-red-dark: #a50f16;
    --ink: #2a2a2a;
    --ink-soft: #555555;
    --paper: #ffffff;
    --tint: #f6dcdd;
    --backdrop: #e9e7e4;
  }
  * { box-sizing: border-box; margin: 0; padding: 0; }
  html, body { width: 1200px; height: 911px; overflow: hidden; }
  body {
    background: var(--backdrop);
    font-family: "Roboto", Arial, sans-serif;
    position: relative;
  }
  .card {
    position: absolute;
    width: 600px;
    height: 343px;
    border-radius: 3px;
    overflow: hidden;
    box-shadow: 0 10px 28px rgba(0,0,0,0.18);
  }
  /* Front */
  .card-front { left: 70px; top: 80px; background: var(--paper); }
  .front-pattern {
    position: absolute;
    left: 250px; top: 0;
    width: 350px; height: 301px;
    background: linear-gradient(135deg, rgba(246,220,221,0) 0%, var(--tint) 45%, rgba(246,220,221,0.55) 100%);
  }
  .holder { position: absolute; left: 40px; top: 36px; }
  .holder-name {
    font-family: "Roboto Condensed", Arial, sans-serif;
    font-weight: 700;
    font-size: 25px;
    color: var(--brand-red);
    text-transform: uppercase;
    letter-spacing: 0.3px;
  }
  .holder-role {
    font-family: "Roboto Condensed", Arial, sans-serif;
    font-size: 13px;
    color: var(--ink);
    margin-top: 2px;
  }
  .divider {
    position: absolute;
    left: 40px; top: 104px;
    width: 300px; height: 1px;
    background: linear-gradient(90deg, var(--brand-red), rgba(208,22,31,0));
  }
  .contacts {
    position: absolute;
    left: 40px; top: 120px;
    display: grid;
    grid-template-columns: 170px 170px;
    row-gap: 6px;
    font-size: 12.5px;
    color: var(--ink-soft);
  }
  .contact-line { display: flex; align-items: center; gap: 7px; white-space: nowrap; }
  .contact-line svg { width: 11px; height: 11px; fill: var(--brand-red); flex: none; }
  .contact-email { grid-column: 1 / 3; padding-left: 18px; }
  .contact-web {
    grid-column: 1 / 3;
    padding-left: 18px;
    color: var(--brand-red);
    letter-spacing: 3px;
    font-size: 12px;
  }
  .brand {
    position: absolute;
    right: 36px; bottom: 62px;
    display: flex; align-items: center; gap: 12px;
  }
  .brand-square { width: 40px; height: 40px; background: var(--brand-red); }
  .brand-name {
    font-family: "Roboto", Arial, sans-serif;
    font-weight: 700;
    font-size: 46px;
    color: var(--ink);
    letter-spacing: -1px;
    line-height: 1;
  }
  .address-band {
    position: absolute;
    left: 0; bottom: 0;
    width: 100%; height: 42px;
    background: linear-gradient(90deg, var(--brand-red-dark), var(--brand-red));
    color: var(--paper);
    font-size: 13.5px;
    display: flex; align-items: center; justify-content: center;
    letter-spacing: 0.2px;
  }
  /* Back */
  .card-back {
    left: 530px; top: 488px;
    background: linear-gradient(120deg, var(--brand-red-dark) 0%, var(--brand-red) 70%, #d81c24 100%);
  }
  .back-brand {
    position: absolute;
    left: 0; top: 0; width: 100%; height: 270px;
    display: flex; align-items: center; justify-content: center; gap: 16px;
  }
  .back-brand .brand-square { background: var(--paper); width: 54px; height: 54px; }
  .back-brand .brand-name { color: var(--paper); font-size: 60px; }
  .services {
    position: absolute;
    left: 36px; bottom: 30px;
    display: flex; align-items: center; gap: 16px;
    color: var(--paper);
    font-size: 20px;
    letter-spacing: 0.2px;
  }
  .services-sep { width: 1px; height: 20px; background: rgba(255,255,255,0.75); }
</style>
</head>
<body>
  <section class="card card-front">
    <div class="front-pattern" role="img" aria-label="Soft pink geometric background pattern"></div>
    <div class="holder">
      <div class="holder-name">Tessa Marlowe</div>
      <div class="holder-role">Business Development Manager</div>
    </div>
    <div class="divider"></div>
    <div class="contacts">
      <div class="contact-line">
        <svg viewBox="0 0 24 24" aria-hidden="true"><path d="M6.6 10.8a15.1 15.1 0 0 0 6.6 6.6l2.2-2.2c.3-.3.7-.4 1-.2 1.1.4 2.3.6 3.6.6.6 0 1 .4 1 1V20c0 .6-.4 1-1 1A17 17 0 0 1 3 4c0-.6.4-1 1-1h3.5c.6 0 1 .4 1 1 0 1.3.2 2.5.6 3.6.1.3 0 .7-.2 1z"/></svg>
        +61 (07) 5550 1234
      </div>
      <div class="contact-line">
        <svg viewBox="0 0 24 24" aria-hidden="true"><path d="M7 2h10a2 2 0 0 1 2 2v16a2 2 0 0 1-2 2H7a2 2 0 0 1-2-2V4a2 2 0 0 1 2-2zm0 3v12h10V5z"/></svg>
        +61 (0)400 555 218
      </div>
      <div class="contact-line">
        <svg viewBox="0 0 24 24" aria-hidden="true"><path d="M6.6 10.8a15.1 15.1 0 0 0 6.6 6.6l2.2-2.2c.3-.3.7-.4 1-.2 1.1.4 2.3.6 3.6.6.6 0 1 .4 1 1V20c0 .6-.4 1-1 1A17 17 0 0 1 3 4c0-.6.4-1 1-1h3.5c.6 0 1 .4 1 1 0 1.3.2 2.5.6 3.6.1.3 0 .7-.2 1z"/></svg>
        +61 (07) 5550 1236
      </div>
      <div class="contact-line">
        <svg viewBox="0 0 24 24" aria-hidden="true"><path d="M6 3h10v5H6zM4 9h16a2 2 0 0 1 2 2v6h-4v4H6v-4H2v-6a2 2 0 0 1 2-2zm4 7v3h8v-3z"/></svg>
        +61 (07) 5550 1239
      </div>
      <div class="contact-line contact-email">tmarlowe@korvalit.com.au</div>
      <div class="contact-line contact-web">www.korvalit.com.au</div>
    </div>
    <div class="brand">
      <span class="brand-square"></span>
      <span class="brand-name">korvalit</span>
    </div>
    <div class="address-band">Level 1, 47 Fernby Street, Carlow Qld 4072</div>
  </section>

  <section class="card card-back">
    <div class="back-brand">
      <span class="brand-square"></span>
      <span class="brand-name">korvalit</span>
    </div>
    <div class="services">
      <span>MapOut</span>
      <span class="services-sep"></span>
      <span>ShipWell</span>
      <span class="services-sep"></span>
      <span>KeepSteady</span>
    </div>
  </section>
</body>
</html>
```